Business card for Luxury Portable Restroom Trailer company

We are a Luxury Portable Restroom Trailer Company Called FALCRIDGE HIRES. Based in Orange County California. We provide portable restroom trailers for events, such as, Weddings, Concerts, Charity events, Sporting events, Tournaments, Corporate events, ect. We rent and Sell the Luxury restrooms. Our colors are white, grey, and Orange. As you will see in the logo we uploaded.
There are 2 people in the company so the names and titles will change for the 3 people but card will remain the same. Here is the information for each Person: Dwight Penner CFO 555 318-0476
next Person: Leon Marchetti VP 555 318-0476
Next Person: Owen Marchetti CEO 555 318-0476
Information to include on the card: Luxury Restroom Trailers Rental and Sales. Weddings, Concerts, Charity, Sporting and Corp. Events.

```html
<!DOCTYPE html>
<html lang="en">
<head>
<meta charset="utf-8">
<title>FALCRIDGE HIRES – Business Card</title>
<link href="https://fonts.googleapis.com/css2?family=Open+Sans:wght@400;600;700;800&display=swap" rel="stylesheet">
<style>
  :root {
    --stage: #232323;
    --card: #2a2a2d;
    --card-deep: #252528;
    --emblem: #32292a;
    --orange: #f26a21;
    --grey: #58585a;
    --grey-light: #8a8a8c;
    --white: #f4f4f4;
    --rule: #9a9a9a;
  }
  * { box-sizing: border-box; margin: 0; padding: 0; }
  html, body {
    width: 1200px; height: 768px; overflow: hidden;
    background: var(--stage);
    font-family: "Open Sans", Arial, sans-serif;
  }
  .canvas { position: relative; width: 1200px; height: 768px; }

  .card {
    position: absolute;
    width: 560px; height: 320px;
    background: var(--card);
    border-radius: 18px;
    overflow: hidden;
    box-shadow: 0 14px 30px rgba(0,0,0,.45);
  }
  .card--front { left: 70px; top: 50px; }
  .card--back { left: 570px; top: 400px; }

  .card__bands { position: absolute; left: 0; bottom: 0; width: 100%; height: 60px; }

  .card__emblem {
    position: absolute; left: 150px; top: -40px; width: 360px; height: 330px;
    border-radius: 50%;
    background: radial-gradient(ellipse at center, var(--emblem) 0%, var(--emblem) 55%, rgba(50,41,42,0) 72%);
  }

  .wordmark {
    display: flex; align-items: center; gap: 10px;
    color: var(--orange);
    font-weight: 800;
    letter-spacing: 1px;
    white-space: nowrap;
  }
  .wordmark__mark { background: var(--orange); flex: none; }
  .card--front .wordmark {
    position: absolute; left: 0; right: 0; top: 118px;
    justify-content: center; font-size: 34px;
  }
  .card--front .wordmark__mark { width: 22px; height: 22px; }

  .card--back .wordmark {
    position: absolute; left: 34px; top: 130px; font-size: 21px;
  }
  .card--back .wordmark__mark { width: 14px; height: 14px; }

  .divider {
    position: absolute; left: 282px; top: 52px; width: 1px; height: 150px;
    background: var(--rule);
  }

  .contact { position: absolute; left: 306px; top: 62px; color: var(--white); }
  .contact__name { font-size: 26px; font-weight: 700; line-height: 1.1; }
  .contact__first { color: var(--orange); }
  .contact__last { color: var(--grey-light); }
  .contact__title { font-size: 14px; font-weight: 600; margin: 2px 0 12px; }
  .contact__list { list-style: none; font-size: 13px; line-height: 1.75; }
  .contact__list li { display: flex; align-items: center; gap: 9px; }
  .contact__list svg { width: 13px; height: 13px; flex: none; fill: var(--orange); }

  .services {
    position: absolute; left: 30px; right: 24px; top: 220px;
    color: var(--white); font-size: 13.5px; line-height: 1.6;
    text-align: center;
  }
  .services__row { display: flex; justify-content: center; flex-wrap: wrap; gap: 4px 12px; }
  .services__item { display: inline-flex; align-items: center; gap: 6px; }
  .services__item::before {
    content: ""; width: 8px; height: 8px; background: var(--orange); flex: none;
  }
</style>
</head>
<body>
<main class="canvas">

  <section class="card card--front" aria-label="Business card front">
    <div class="card__emblem" role="img" aria-label="Large faint brand emblem decoration"></div>
    <div class="wordmark"><span class="wordmark__mark"></span>FALCRIDGE HIRES</div>
    <svg class="card__bands" viewBox="0 0 560 60" preserveAspectRatio="none" aria-hidden="true">
      <polygon points="330,22 560,4 560,60 330,60" fill="var(--grey)"/>
      <polygon points="0,44 300,22 330,22 330,60 0,60" fill="var(--orange)"/>
    </svg>
  </section>

  <section class="card card--back" aria-label="Business card back">
    <div class="wordmark"><span class="wordmark__mark"></span>FALCRIDGE HIRES</div>
    <div class="divider"></div>
    <div class="contact">
      <h1 class="contact__name"><span class="contact__first">Dwight</span> <span class="contact__last">Penner</span></h1>
      <p class="contact__title">CFO</p>
      <ul class="contact__list">
        <li>
          <svg viewBox="0 0 24 24" aria-hidden="true"><path d="M6.6 10.8a15 15 0 0 0 6.6 6.6l2.2-2.2a1 1 0 0 1 1-.25 11.4 11.4 0 0 0 3.6.57 1 1 0 0 1 1 1V20a1 1 0 0 1-1 1A17 17 0 0 1 3 4a1 1 0 0 1 1-1h3.5a1 1 0 0 1 1 1c0 1.25.2 2.45.57 3.57a1 1 0 0 1-.25 1z"/></svg>
          555 318-0476
        </li>
        <li>
          <svg viewBox="0 0 24 24" aria-hidden="true"><path d="M2 5h20v14H2z M4 7v.5l8 5 8-5V7z" fill-rule="evenodd"/></svg>
          info@falcridgehires.com
        </li>
        <li>
          <svg viewBox="0 0 24 24" aria-hidden="true"><path d="M12 2a10 10 0 1 0 0 20 10 10 0 0 0 0-20zm0 2c.9 0 2.2 2 2.7 5H9.3C9.8 6 11.1 4 12 4zM4.3 11h3a17 17 0 0 0 0 2h-3a8 8 0 0 1 0-2zm5 0h5.4a15 15 0 0 1 0 2H9.3a15 15 0 0 1 0-2zm7.4 0h3a8 8 0 0 1 0 2h-3a17 17 0 0 0 0-2zM9.3 15h5.4c-.5 3-1.8 5-2.7 5s-2.2-2-2.7-5z"/></svg>
          www.falcridgehires.com
        </li>
      </ul>
    </div>
    <div class="services">
      <div class="services__row">
        <span class="services__item">Luxury Restroom Trailers Rental and Sales</span>
      </div>
      <div class="services__row">
        <span class="services__item">Weddings</span>
        <span class="services__item">Concerts</span>
        <span class="services__item">Charity</span>
        <span class="services__item">Sporting and Corp</span>
        <span class="services__item">Events</span>
      </div>
    </div>
    <svg class="card__bands" viewBox="0 0 560 60" preserveAspectRatio="none" aria-hidden="true">
      <polygon points="330,22 560,4 560,60 330,60" fill="var(--grey)"/>
      <polygon points="0,44 300,22 330,22 330,60 0,60" fill="var(--orange)"/>
    </svg>
  </section>

</main>
</body>
</html>
```